Heavy Duty Repairs Poster

Good afternoon - I'm looking for a poster , design to set up around different areas. The Poster must consist of the following
- Heavy duty repairs
- Pictures of Semi trucks , heavy construction equipment , trailers
- Agriculture
- All north American equipment ( see attached pictures)
- Brief Descriptions in bullet point forms
CVIPS
WELDING
AIR CONDITIONING
ENGINE REBUILDS
DIAGONSTICS
FLEET MANAGMENT
TIRE REPAIR AND SALES
ELECTRICAL , HYDRALIC , POWER TRAIN SERVICE AND REPAIRS
PART SALES
FLEET MAINTINACE
DELTEING AND TUNING
AFTER MARKET INSTALLS OUTFITTING
ONSITE & OFFSITE REPAIRS
FULL RECERTIFACTION OVERHAULING
Warranty Approved

Target Market(s)

Heavy Duty Truck , Equipment , Agriculture Owners

Industry/Entity Type

Heavy Duty Repairs

Colors
EB3D1F
EC4F4E
F09395
F8D3D4
FCEDEE

Requirements
Must have
• Pictures of : Semi trucks and trailer , Construction heavy equipment , agriculture equipment
Nice to have
• Flashy and stands out

```html
<!DOCTYPE html>
<html lang="en">
<head>
<meta charset="utf-8">
<title>Ridgeway Mechanical Services – Heavy Duty Repairs Poster</title>
<link href="https://fonts.googleapis.com/css2?family=Montserrat:wght@500;600;700;900&family=Russo+One&display=swap" rel="stylesheet">
<style>
  :root{
    --red:#eb1c1f;
    --black:#0d0d0d;
    --body:#aeb3a6;
    --body-light:#bcc1b5;
    --frame:#9a9a9a;
    --frame-light:#c9c9c9;
    --label:#3f4240;
    --white:#ffffff;
    --icon-bg:#f6f4f1;
    --page:#ececec;
  }
  *{margin:0;padding:0;box-sizing:border-box}
  html,body{width:803px;height:1200px;overflow:hidden;background:var(--page)}
  .poster{position:relative;width:803px;height:1200px;background:linear-gradient(180deg,var(--body) 0%,var(--body-light) 60%,var(--body) 100%);overflow:hidden;font-family:"Montserrat",sans-serif}
  .top-bar{position:absolute;left:0;top:0;width:100%;height:30px;background:linear-gradient(180deg,var(--frame-light),var(--frame))}
  .hero-photo{position:absolute;left:0;top:30px;width:100%;height:534px;
    background:linear-gradient(180deg,#6f8591 0%,#a3aaa5 38%,#8b6f66 62%,#5b4c49 80%,#3f3d3d 100%)}
  .hero-curves{position:absolute;left:0;top:380px;width:803px;height:200px}
  .header-plate{position:absolute;left:0;top:0;width:803px;height:170px}
  .phone{position:absolute;top:42px;left:0;width:100%;text-align:center;font-family:"Russo One",sans-serif;color:var(--red);font-size:25px;letter-spacing:1px}
  .brand-name{position:absolute;top:84px;left:0;width:100%;text-align:center;color:var(--white);font-size:14px;font-weight:600}
  .brand-place{position:absolute;top:104px;left:0;width:100%;text-align:center;color:var(--white);font-size:12px;font-weight:600}
  .title{position:absolute;top:600px;left:0;width:100%;text-align:center;font-weight:900;color:var(--black);line-height:60px;letter-spacing:-1px;white-space:nowrap}
  .title .line-1,.title .line-2{display:block;font-size:50px}
  .tagline{position:absolute;top:734px;left:174px;width:456px;height:54px;border-radius:27px;background:var(--red);border:3px solid var(--white);color:var(--white);font-weight:900;font-size:33px;text-align:center;line-height:48px;letter-spacing:.5px;white-space:nowrap}
  .tag-gear{position:absolute;top:739px;width:44px;height:44px}
  .tag-gear.left{left:126px}
  .tag-gear.right{left:634px}
  .grid-lines{position:absolute;left:0;top:0;width:803px;height:1200px}
  .service{position:absolute;width:130px;text-align:center}
  .service-icon{display:block;margin:0 auto;width:64px;height:64px}
  .service-label{display:block;margin-top:5px;font-size:10.5px;font-weight:600;color:var(--label);line-height:12.5px;text-transform:uppercase}
  .footer{position:absolute;left:0;bottom:0;width:100%;height:44px;background:var(--black);color:var(--white);text-align:center;font-size:19px;font-weight:500;line-height:44px;letter-spacing:1.5px}
  .footer .domain{color:var(--red);font-weight:700}
</style>
</head>
<body>
<svg width="0" height="0" style="position:absolute" aria-hidden="true">
  <defs>
    <symbol id="gear" viewBox="0 0 24 24"><path fill="currentColor" d="M10 1h4l.6 3 2.3 1 2.6-1.7 2.8 2.8L20.6 8.7l1 2.3 2.4.6v3.8l-2.4.6-1 2.3 1.7 2.6-2.8 2.8-2.6-1.7-2.3 1-.6 2.6h-4l-.6-2.6-2.3-1-2.6 1.7-2.8-2.8 1.7-2.6-1-2.3L0 14.8V11l2.6-.6 1-2.3L1.8 5.1 4.6 2.3 7.2 4l2.3-1z"/><circle cx="12" cy="12.5" r="4" fill="#f6f4f1"/></symbol>
    <symbol id="gear-badge" viewBox="0 0 24 24"><path fill="#0d0d0d" d="M10 1h4l.6 3 2.3 1 2.6-1.7 2.8 2.8L20.6 8.7l1 2.3 2.4.6v3.8l-2.4.6-1 2.3 1.7 2.6-2.8 2.8-2.6-1.7-2.3 1-.6 2.6h-4l-.6-2.6-2.3-1-2.6 1.7-2.8-2.8 1.7-2.6-1-2.3L0 14.8V11l2.6-.6 1-2.3L1.8 5.1 4.6 2.3 7.2 4l2.3-1z"/><g stroke="#fff" stroke-width="1.6" stroke-linecap="round"><path d="M8 8l8 9M16 8l-8 9"/></g></symbol>
    <symbol id="wrench" viewBox="0 0 24 24"><g stroke="currentColor" stroke-width="3" stroke-linecap="round"><path d="M5 5l14 14"/><path d="M19 5L5 19"/></g><circle cx="4.5" cy="4.5" r="3" fill="currentColor"/><circle cx="19.5" cy="4.5" r="3" fill="currentColor"/></symbol>
    <symbol id="bolt" viewBox="0 0 24 24"><circle cx="12" cy="12" r="10" fill="none" stroke="currentColor" stroke-width="2"/><path fill="currentColor" d="M13 3L6 13h5l-1 8 7-10h-5z"/></symbol>
    <symbol id="clock" viewBox="0 0 24 24"><circle cx="12" cy="12" r="10" fill="currentColor"/><circle cx="12" cy="12" r="7" fill="none" stroke="#f6f4f1" stroke-width="1.6"/><path d="M12 8v4l3 2" stroke="#f6f4f1" stroke-width="1.6" fill="none"/></symbol>
    <symbol id="tire" viewBox="0 0 24 24"><circle cx="12" cy="12" r="10" fill="currentColor"/><circle cx="12" cy="12" r="5" fill="#f6f4f1"/><circle cx="12" cy="12" r="2" fill="currentColor"/></symbol>
    <symbol id="bin" viewBox="0 0 24 24"><rect x="5" y="7" width="14" height="15" rx="2" fill="currentColor"/><rect x="3" y="3" width="18" height="3" fill="currentColor"/><path d="M9 10v9M12 10v9M15 10v9" stroke="#f6f4f1" stroke-width="1.4"/></symbol>
    <symbol id="truck" viewBox="0 0 24 24"><rect x="1" y="5" width="13" height="11" fill="currentColor"/><path fill="currentColor" d="M14 9h5l4 4v3h-9z"/><circle cx="6" cy="19" r="2.5" fill="currentColor"/><circle cx="18" cy="19" r="2.5" fill="currentColor"/></symbol>
    <symbol id="box" viewBox="0 0 24 24"><rect x="2" y="5" width="20" height="9" rx="2" fill="currentColor"/><path d="M6 16v5M10 16v5M14 16v5M18 16v5" stroke="currentColor" stroke-width="1.6"/></symbol>
  </defs>
</svg>

<main class="poster">
  <div class="top-bar"></div>
  <div class="hero-photo" role="img" aria-label="Photo: red semi truck with trailer on a highway at dusk, a mechanic in hard hat and safety vest on the left giving a thumbs up, and a smiling mechanic in blue coveralls on the right"></div>

  <svg class="hero-curves" viewBox="0 0 803 200" aria-hidden="true">
    <path d="M0 184 Q401 290 803 184 L803 200 L0 200Z" fill="var(--body)"/>
    <path d="M-5 150 Q401 300 808 150" fill="none" stroke="var(--red)" stroke-width="7"/>
    <path d="M0 90 Q70 150 170 165 Q90 175 0 200Z" fill="var(--red)"/>
    <path d="M0 140 Q80 180 170 168 Q90 195 0 200Z" fill="var(--black)"/>
    <path d="M803 90 Q740 150 640 165 Q720 175 803 200Z" fill="var(--red)"/>
    <path d="M803 140 Q720 180 640 168 Q720 195 803 200Z" fill="var(--black)"/>
  </svg>

  <svg class="header-plate" viewBox="0 0 803 170" aria-hidden="true">
    <path d="M238 26 H565 L525 148 H278Z" fill="var(--frame)"/>
    <path d="M250 30 H553 L518 140 H285Z" fill="var(--frame-light)"/>
    <path d="M263 30 H540 L510 132 H292Z" fill="var(--black)"/>
  </svg>
  <div class="phone">555-014-2287</div>
  <div class="brand-name">Ridgeway Mechanical Services</div>
  <div class="brand-place">Pinecrest , Alberta</div>

  <h1 class="title"><span class="line-1">RIDGEWAY MECHANICAL</span><span class="line-2">SERVICES</span></h1>

  <svg class="tag-gear left" viewBox="0 0 24 24" aria-hidden="true"><use href="#gear-badge"/></svg>
  <div class="tagline">HEAVY DUTY REPAIRS</div>
  <svg class="tag-gear right" viewBox="0 0 24 24" aria-hidden="true"><use href="#gear-badge"/></svg>

  <svg class="grid-lines" viewBox="0 0 803 1200" aria-hidden="true">
    <g stroke="#8c9186" stroke-width="1" stroke-dasharray="4 3">
      <path d="M203 810v340M338 810v340M466 810v340M595 810v340"/>
    </g>
    <g stroke="#8c9186" stroke-width="1">
      <path d="M70 910H725M70 1020H725"/>
    </g>
  </svg>

  <section aria-label="Services">
    <div class="service" style="left:71px;top:805px"><svg class="service-icon" viewBox="0 0 64 64" style="color:var(--red)"><circle cx="32" cy="32" r="29" fill="var(--icon-bg)" stroke="var(--red)" stroke-width="3.5"/><use href="#truck" x="18" y="18" width="28" height="28"/></svg><span class="service-label">CVIPS</span></div>
    <div class="service" style="left:206px;top:805px"><svg class="service-icon" viewBox="0 0 64 64" style="color:var(--red)"><circle cx="32" cy="32" r="29" fill="var(--icon-bg)" stroke="var(--red)" stroke-width="3.5"/><use href="#gear" x="18" y="18" width="28" height="28"/></svg><span class="service-label">WELDING</span></div>
    <div class="service" style="left:336px;top:805px"><svg class="service-icon" viewBox="0 0 64 64" style="color:var(--red)"><circle cx="32" cy="32" r="29" fill="var(--icon-bg)" stroke="var(--red)" stroke-width="3.5"/><use href="#clock" x="18" y="18" width="28" height="28"/></svg><span class="service-label">AIR<br>CONDITIONING</span></div>
    <div class="service" style="left:465px;top:805px"><svg class="service-icon" viewBox="0 0 64 64" style="color:var(--red)"><circle cx="32" cy="32" r="29" fill="var(--icon-bg)" stroke="var(--red)" stroke-width="3.5"/><use href="#tire" x="18" y="18" width="28" height="28"/></svg><span class="service-label">ENGINE<br>REBUILDS</span></div>
    <div class="service" style="left:594px;top:805px"><svg class="service-icon" viewBox="0 0 64 64" style="color:var(--red)"><circle cx="32" cy="32" r="29" fill="var(--icon-bg)" stroke="var(--red)" stroke-width="3.5"/><use href="#truck" x="18" y="18" width="28" height="28"/></svg><span class="service-label">DIAGONSTICS</span></div>

    <div class="service" style="left:71px;top:914px"><svg class="service-icon" viewBox="0 0 64 64" style="color:var(--red)"><circle cx="32" cy="32" r="29" fill="var(--icon-bg)" stroke="var(--red)" stroke-width="3.5"/><use href="#truck" x="18" y="18" width="28" height="28"/></svg><span class="service-label">FLEET<br>MANAGMENT</span></div>
    <div class="service" style="left:206px;top:914px"><svg class="service-icon" viewBox="0 0 64 64" style="color:var(--red)"><circle cx="32" cy="32" r="29" fill="var(--icon-bg)" stroke="var(--red)" stroke-width="3.5"/><use href="#box" x="18" y="18" width="28" height="28"/></svg><span class="service-label">PART<br>SALES</span></div>
    <div class="service" style="left:336px;top:914px"><svg class="service-icon" viewBox="0 0 64 64" style="color:var(--red)"><circle cx="32" cy="32" r="29" fill="var(--icon-bg)" stroke="var(--red)" stroke-width="3.5"/><use href="#wrench" x="18" y="18" width="28" height="28"/></svg><span class="service-label">FLEET<br>MAINTINACE</span></div>
    <div class="service" style="left:465px;top:914px"><svg class="service-icon" viewBox="0 0 64 64" style="color:var(--red)"><circle cx="32" cy="32" r="29" fill="var(--icon-bg)" stroke="var(--red)" stroke-width="3.5"/><use href="#gear" x="18" y="18" width="28" height="28"/></svg><span class="service-label">TIRE REPAIR<br>AND SALES</span></div>
    <div class="service" style="left:594px;top:914px"><svg class="service-icon" viewBox="0 0 64 64" style="color:var(--red)"><circle cx="32" cy="32" r="29" fill="var(--icon-bg)" stroke="var(--red)" stroke-width="3.5"/><use href="#bin" x="18" y="18" width="28" height="28"/></svg><span class="service-label">ELECTRICAL<br>HYDRALIC</span></div>

    <div class="service" style="left:71px;top:1024px"><svg class="service-icon" viewBox="0 0 64 64" style="color:var(--red)"><circle cx="32" cy="32" r="29" fill="var(--icon-bg)" stroke="var(--red)" stroke-width="3.5"/><use href="#truck" x="18" y="18" width="28" height="28"/></svg><span class="service-label">POWER TRAIN<br>SERVICE<br>AND REPAIRS</span></div>
    <div class="service" style="left:206px;top:1024px"><svg class="service-icon" viewBox="0 0 64 64" style="color:var(--red)"><circle cx="32" cy="32" r="29" fill="var(--icon-bg)" stroke="var(--red)" stroke-width="3.5"/><use href="#wrench" x="18" y="18" width="28" height="28"/></svg><span class="service-label">DELTEING<br>AND<br>TUNING</span></div>
    <div class="service" style="left:336px;top:1024px"><svg class="service-icon" viewBox="0 0 64 64" style="color:var(--red)"><circle cx="32" cy="32" r="29" fill="var(--icon-bg)" stroke="var(--red)" stroke-width="3.5"/><use href="#bolt" x="18" y="18" width="28" height="28"/></svg><span class="service-label">ONSITE &amp;<br>OFFSITE<br>REPAIRS</span></div>
    <div class="service" style="left:465px;top:1024px"><svg class="service-icon" viewBox="0 0 64 64" style="color:var(--red)"><circle cx="32" cy="32" r="29" fill="var(--icon-bg)" stroke="var(--red)" stroke-width="3.5"/><use href="#box" x="18" y="18" width="28" height="28"/></svg><span class="service-label">FULL<br>RECERTIFACTION<br>OVERHAULING</span></div>
    <div class="service" style="left:594px;top:1024px"><svg class="service-icon" viewBox="0 0 64 64" style="color:var(--red)"><circle cx="32" cy="32" r="29" fill="var(--icon-bg)" stroke="var(--red)" stroke-width="3.5"/><use href="#wrench" x="18" y="18" width="28" height="28"/></svg><span class="service-label">AFTER MARKET<br>INSTALLS<br>OUTFITTING</span></div>
  </section>

  <footer class="footer">www.<span class="domain">ridgewaymechanicalservices</span>.co</footer>
</main>
</body>
</html>
```